Flat Belly Design Graphics for Social

I want to create 9 social media graphics (new Instagram size 4:5 (1080 x 1350 pixels) focusing on our Flat Belly Graphics, using the pics attached. Use the attached pics, NO RANDOM STOCK PHOTOGRAPHY. For the color scheme of the graphics, the color palette is attached. YOU MUST POST ALL 9 GRAPHICS IN ONE ENTRY.
Using the 3 titles below, create one set of graphics. 1) with all text, then for the others, use the pictures as detailed below in IMPORTANT:
1. Ten-Week Bright Morning Reboot
2. The Quick Garden Kitchen Menu Guide
3. Studio Habits for Lasting Energy Past Midlife - Zero Gym Needed
IMPORTANT:
Only use RK Pic 1 and RK Pic 2 with the title, Ten-Week Bright Morning Reboot
Only use meal plan1 and meal plan2 pics with the title, Quick Garden Kitchen Menu Guide
Only use studio habits 1 and studio habits 2 pics with the title, Studio Habits for Lasting Energy Past Midlife - Zero Gym Needed
women over 40

```html
<!DOCTYPE html>
<html lang="en">
<head>
<meta charset="utf-8">
<title>Morning Reboot Social Set</title>
<link href="https://fonts.googleapis.com/css2?family=Oswald:wght@500;600;700&family=Montserrat:ital,wght@0,600;0,700;0,800;0,900;1,700;1,800&family=Allura&display=swap" rel="stylesheet">
<style>
  :root {
    --stage: #272727;
    --blush: #f7dce2;
    --blush-soft: #fbe5ea;
    --rose: #e4a0b6;
    --rose-bright: #ef8bb0;
    --berry: #cc5b8c;
    --pine: #195c50;
    --pine-deep: #1f5a52;
    --mist: #efefef;
    --white: #ffffff;
  }
  * { margin: 0; padding: 0; box-sizing: border-box; }
  html, body { width: 960px; height: 1200px; overflow: hidden; background: var(--stage); }
  .canvas { position: relative; width: 960px; height: 1200px; background: var(--stage); }
  .tile { position: absolute; width: 231px; height: 289px; overflow: hidden; }
  .col-1 { left: 110px; } .col-2 { left: 363px; } .col-3 { left: 617px; }
  .row-1 { top: 132px; } .row-2 { top: 452px; } .row-3 { top: 772px; }
  .panel { position: absolute; inset: 0; }
  .line { position: absolute; left: 0; right: 0; text-align: center; white-space: nowrap; line-height: 1; }
  .condensed { font-family: "Oswald", sans-serif; font-weight: 700; letter-spacing: -0.5px; }
  .wide { font-family: "Montserrat", sans-serif; font-weight: 800; }
  .script { font-family: "Allura", cursive; font-weight: 400; }
  .pine { color: var(--pine); } .berry { color: var(--berry); } .rose { color: var(--rose-bright); } .light { color: var(--white); }
  .photo { position: absolute; }

  /* Tile 1 — all-text reboot */
  .reboot-type { background: var(--rose); }
  .reboot-type .panel { background: var(--blush); border-radius: 58px 0 58px 0; }
  .reboot-type .t1 { top: 40px; font-size: 29px; font-weight: 900; }
  .reboot-type .t2 { top: 83px; font-size: 42px; }
  .reboot-type .t3 { top: 138px; font-size: 50px; }
  .reboot-type .t4 { top: 210px; font-size: 44px; font-weight: 900; text-shadow: 3px 4px 5px rgba(140,40,80,.35); }

  /* Tile 2 — all-text menu guide */
  .menu-type { background: var(--blush); }
  .menu-type .panel { background: var(--berry); border-radius: 0 58px 0 58px; }
  .menu-type .stack { position: absolute; left: 13px; top: 33px; width: 112px; height: 222px; background: var(--blush-soft); }
  .menu-type .stack::after { content: ""; position: absolute; right: -8px; top: 105px; border-left: 8px solid var(--blush-soft); border-top: 8px solid transparent; border-bottom: 8px solid transparent; }
  .menu-type .stack .line { font-family: "Oswald", sans-serif; font-weight: 700; color: var(--pine); letter-spacing: -1px; }
  .menu-type .s1 { top: 16px; font-size: 44px; }
  .menu-type .s2 { top: 82px; font-size: 38px; }
  .menu-type .s3 { top: 160px; font-size: 30px; }
  .menu-type .side { position: absolute; left: 136px; top: 80px; font-family: "Montserrat", sans-serif; font-weight: 600; color: var(--blush-soft); font-size: 18px; line-height: 36px; }

  /* Tile 3 — all-text studio habits */
  .habits-type { background: var(--rose-bright); }
  .habits-type .panel { background: var(--blush-soft); border-radius: 58px 0 58px 0; }
  .habits-type .h1 { top: 36px; font-size: 20px; font-weight: 500; }
  .habits-type .h2 { top: 70px; font-size: 31px; }
  .habits-type .h3 { top: 112px; font-size: 37px; }
  .habits-type .rule { position: absolute; left: 19px; right: 19px; height: 1px; background: var(--berry); }
  .habits-type .r1 { top: 170px; } .habits-type .r2 { top: 262px; }
  .habits-type .tag { top: 178px; font-family: "Montserrat", sans-serif; font-style: italic; font-weight: 800; font-size: 28px; line-height: 40px; }

  /* Tile 4 — portrait reboot */
  .reboot-portrait { background: var(--rose); }
  .reboot-portrait .panel { background: var(--blush); border-radius: 0 46px 0 46px; }
  .reboot-portrait .photo { left: 25px; top: 0; width: 190px; height: 235px; background: linear-gradient(180deg, #2a1f1d 0%, #6b4a3d 28%, #f3efee 55%, #ffffff 80%, rgba(247,220,226,0) 100%); border-radius: 90px 90px 10px 10px; }
  .reboot-portrait .p1 { top: 188px; font-size: 30px; font-weight: 800; }
  .reboot-portrait .swash { position: absolute; left: 60px; top: 222px; }
  .reboot-portrait .p2 { top: 231px; font-size: 19px; }
  .reboot-portrait .p3 { top: 256px; font-size: 17px; }

  /* Tile 5 — food menu guide */
  .menu-photo { background: var(--blush); }
  .menu-photo .panel { background: var(--mist); border-radius: 0 0 46px 0; }
  .menu-photo .photo { left: 19px; top: 29px; width: 193px; height: 126px; background: linear-gradient(135deg, #f2c4b4 0%, #6a3e2a 40%, #c2412f 60%, #4c2c1f 100%); }
  .menu-photo .m1 { top: 174px; font-size: 19px; }
  .menu-photo .m1 em { font-style: italic; font-weight: 600; }
  .menu-photo .m2 { top: 200px; font-size: 20px; color: var(--rose-bright); }
  .menu-photo .m3 { top: 236px; font-size: 26px; }

  /* Tile 6 — studio habits duo */
  .habits-duo { background: var(--rose); }
  .habits-duo .panel { background: var(--blush); border-radius: 46px 0 0 0; }
  .habits-duo .photo { left: 0; top: 120px; width: 231px; height: 169px; background: linear-gradient(90deg, #3a2622 0%, #a86f57 35%, #e6c7b7 60%, #7a4a3a 85%, #caa08e 100%); border-radius: 60px 0 0 0; }
  .habits-duo .d1 { top: 22px; font-family: "Montserrat", sans-serif; font-weight: 700; font-size: 15px; }
  .habits-duo .d2 { top: 40px; font-size: 19px; }
  .habits-duo .d3 { top: 58px; font-family: "Montserrat", sans-serif; font-weight: 700; font-size: 22px; color: var(--rose-bright); }
  .habits-duo .pill { position: absolute; left: 10px; right: 10px; top: 88px; height: 30px; border-radius: 15px; background: var(--rose); box-shadow: 0 3px 4px rgba(140,40,80,.4); font-family: "Montserrat", sans-serif; font-weight: 600; font-size: 15px; color: var(--white); text-align: center; line-height: 30px; z-index: 2; }

  /* Tile 7 — full-bleed reboot */
  .reboot-full { background: var(--blush-soft); }
  .reboot-full .photo { inset: 0; background: linear-gradient(180deg, #6b3f2b 0%, #b08068 30%, #f2eeec 55%, #d9d2cf 72%, #3b2a24 100%); border-radius: 46px 0 46px 0; }
  .reboot-full .f { position: absolute; font-family: "Oswald", sans-serif; font-weight: 600; color: var(--white); line-height: 0.95; }
  .reboot-full .f1 { left: 14px; top: 18px; font-size: 28px; }
  .reboot-full .f2 { right: 8px; top: 18px; font-size: 28px; text-align: right; }
  .reboot-full .f3 { left: 0; right: 0; top: 228px; font-size: 40px; text-align: center; }

  /* Tile 8 — deep green menu guide */
  .menu-bold { background: var(--rose); }
  .menu-bold .photo { inset: 0; background: linear-gradient(160deg, #2c5a4d 0%, var(--pine-deep) 45%, #2b4d40 100%); border-radius: 0 46px 0 46px; }
  .menu-bold .b1 { top: 42px; font-size: 32px; }
  .menu-bold .big { font-family: "Montserrat", sans-serif; font-weight: 900; color: var(--white); font-size: 36px; }
  .menu-bold .b2 { top: 94px; } .menu-bold .b3 { top: 150px; } .menu-bold .b4 { top: 206px; }

  /* Tile 9 — studio habits feature */
  .habits-feature { background: var(--rose); }
  .habits-feature .panel { background: var(--blush); border-radius: 46px 0 46px 0; }
  .habits-feature .photo { left: 0; top: 124px; width: 130px; height: 165px; background: linear-gradient(90deg, #4a2e25 0%, #c79884 45%, #e8cdbf 70%, #a77a66 100%); }
  .habits-feature .e1 { top: 14px; font-family: "Montserrat", sans-serif; font-weight: 700; font-size: 27px; }
  .habits-feature .e2 { top: 48px; font-family: "Montserrat", sans-serif; font-weight: 700; font-size: 23px; }
  .habits-feature .e3 { top: 78px; font-size: 34px; color: var(--berry); }
  .habits-feature .right { position: absolute; left: 128px; width: 103px; text-align: center; line-height: 1; }
  .habits-feature .e4 { top: 130px; font-family: "Montserrat", sans-serif; font-weight: 600; font-size: 19px; color: var(--rose-bright); }
  .habits-feature .e5 { top: 160px; font-family: "Montserrat", sans-serif; font-weight: 700; font-size: 19px; color: var(--rose-bright); }
  .habits-feature .rule { position: absolute; left: 134px; width: 76px; top: 208px; height: 1px; background: var(--rose-bright); }
  .habits-feature .e6 { top: 220px; font-family: "Montserrat", sans-serif; font-weight: 600; font-size: 14px; color: var(--pine); line-height: 18px; }
</style>
</head>
<body>
<main class="canvas">

  <section class="tile col-1 row-1 reboot-type">
    <div class="panel"></div>
    <p class="line wide pine t1">TEN-WEEK</p>
    <p class="line condensed berry t2">BRIGHT</p>
    <p class="line condensed pine t3">MORNING</p>
    <p class="line wide berry t4">REBOOT</p>
  </section>

  <section class="tile col-2 row-1 menu-type">
    <div class="panel"></div>
    <div class="stack">
      <p class="line s1">THE</p>
      <p class="line s2">QUICK</p>
      <p class="line s3">GARDEN</p>
    </div>
    <p class="side">KITCHEN<br>MENU<br>GUIDE</p>
  </section>

  <section class="tile col-3 row-1 habits-type">
    <div class="panel"></div>
    <p class="line condensed rose h1">Studio Habits for</p>
    <p class="line condensed pine h2">LASTING ENERGY</p>
    <p class="line condensed rose h3">PAST MIDLIFE</p>
    <span class="rule r1"></span>
    <p class="line pine tag">Zero Gym<br>Needed</p>
    <span class="rule r2"></span>
  </section>

  <section class="tile col-1 row-2 reboot-portrait">
    <div class="panel"></div>
    <div class="photo" role="img" aria-label="Smiling woman in a white cropped sweater pointing to her waist"></div>
    <p class="line wide pine p1">TEN-WEEK</p>
    <svg class="swash" width="118" height="6" viewBox="0 0 118 6" aria-hidden="true"><path d="M2 5 Q59 -1 116 3" stroke="#ef8bb0" stroke-width="2.5" fill="none" stroke-linecap="round"/></svg>
    <p class="line wide berry p2">BRIGHT MORNING</p>
    <p class="line wide berry p3">REBOOT</p>
  </section>

  <section class="tile col-2 row-2 menu-photo">
    <div class="panel"></div>
    <div class="photo" role="img" aria-label="Overhead table of chicken, berries, vegetables and a printed menu sheet"></div>
    <p class="line wide pine m1">THE <em>QUICK</em></p>
    <p class="line wide m2">GARDEN KITCHEN</p>
    <p class="line wide pine m3">MENU GUIDE</p>
  </section>

  <section class="tile col-3 row-2 habits-duo">
    <div class="panel"></div>
    <p class="line pine d1">STUDIO HABITS</p>
    <p class="line script berry d2">for Lasting Energy</p>
    <p class="line d3">PAST MIDLIFE</p>
    <p class="pill">ZERO GYM NEEDED</p>
    <div class="photo" role="img" aria-label="Two women sharing a secret, one whispering and one looking surprised"></div>
  </section>

  <section class="tile col-1 row-3 reboot-full">
    <div class="photo" role="img" aria-label="Smiling woman in a white cropped sweater pointing to her waist in a warm kitchen"></div>
    <p class="f f1">TEN-<br>WEEK</p>
    <p class="f f2">BRIGHT<br>MORNING</p>
    <p class="f f3">REBOOT</p>
  </section>

  <section class="tile col-2 row-3 menu-bold">
    <div class="photo" role="img" aria-label="Tinted spread of fresh vegetables around a menu notebook"></div>
    <p class="line script light b1">The Quick Garden</p>
    <p class="line big b2">KITCHEN</p>
    <p class="line big b3">MENU</p>
    <p class="line big b4">GUIDE</p>
  </section>

  <section class="tile col-3 row-3 habits-feature">
    <div class="panel"></div>
    <p class="line pine e1">STUDIO</p>
    <p class="line pine e2">HABITS FOR</p>
    <p class="line script e3">Lasting Energy</p>
    <div class="photo" role="img" aria-label="Two women, one whispering to the other who looks excited"></div>
    <p class="right e4">PAST</p>
    <p class="right e5">MIDLIFE</p>
    <span class="rule"></span>
    <p class="right e6">ZERO<br>GYM<br>NEEDED</p>
  </section>

</main>
</body>
</html>
```